International Clinical Software Company needs a new business card design

We are looking for a new business card design for our company that has recently expanded into the UK market, making us a multinational company.
After having rebranded our website and produced a new style guide, we are looking for a business card that is creative and attention grabbing, while being consistent with the style and colour scheme used on the new website, www.plumvora.example
We produce care management technology for the aged care market, but the main aspect we aim to communicate is the human element of our software, and the way it assists in providing better care for aged people, and stronger relationships between aged people and the staff that care for them.
Our current business card is a dark green with gold text, which makes the text quite difficult to read, not very aesthetically appealing and the colour scheme looks quite dated.
We would like something fresh and modern, that can still be colourful but doesn't use large blocks of dark colour, and uses the colours within our logo.
Something tying in with the leaves that are used in our logo could work quite nicely, along with the Autumn/Fall colours of soft greens, yellows and reds (also in our existing logo). However also happy to look at fresh, completely out of the box ideas we may not have yet considered.
Target Market(s)
The people that receive this business card work in the aged card or health industry and are either corporate/management level staff or clinical (Registered Nurses, care workers etc.)
Industry/Entity Type
Health Product
Contact Information for Business Card
Company Name - BrindlewayCare
Company locations: United Kingdom, Australia, New Zealand
Staff Details:
Staff name: Derek Mallow
Staff job title: Executive Chairman
Staff email: d.mallow@plumvora.example
Office phone number: 01742 918576
Font styles to use
Other font styles liked:
- Calibri
Requirements
Must have
- Must include the BrindlewayCare brand name in it's current font
- Must include logo (3 leaves in gold circle)
- Must include Business Card Details
Nice to have
- Elements of gold
- White space
- Something autumn themed but not too cliched
Should not have
- No blue - used by a major competitor and we would like to differentiate from them
- Large blocks of dark green colour (the green that appears in our leaves on the logo on our current business card is the background colour and it is far too dark)

```html
<!DOCTYPE html>
<html lang="en">
<head>
<meta charset="utf-8">
<title>BrindlewayCare business card</title>
<link rel="stylesheet" href="https://fonts.googleapis.com/css2?family=Lato:wght@400;700&display=swap">
<style>
  :root {
    --stage-top: #262626;
    --stage-bottom: #050505;
    --card-white: #f3f3f3;
    --gold: #b39c70;
    --gold-soft: #c9ae78;
    --leaf-amber: #c79a4e;
    --leaf-olive: #a99a5a;
    --name-red: #7a1228;
    --title-green: #3d6b12;
    --ink: #333333;
    --white: #ffffff;
  }
  * { margin: 0; padding: 0; box-sizing: border-box; }
  html, body { width: 1200px; height: 900px; overflow: hidden; }
  body {
    background: linear-gradient(180deg, var(--stage-top) 0%, #1a1a1a 55%, var(--stage-bottom) 100%);
    font-family: "Lato", sans-serif;
    position: relative;
  }
  .card {
    position: absolute;
    top: 184px;
    height: 490px;
    border-radius: 14px;
    overflow: hidden;
  }
  .card-front {
    left: 299px;
    width: 301px;
    background: var(--card-white);
    text-align: center;
    color: var(--ink);
  }
  .brand-circle {
    position: absolute;
    left: 108px; top: 32px;
    width: 86px; height: 86px;
    border: 2px solid var(--gold);
    border-radius: 50%;
  }
  .brand-name {
    position: absolute;
    left: 0; right: 0; top: 128px;
    font-size: 29px;
    font-weight: 400;
    color: var(--gold);
    letter-spacing: 0.5px;
  }
  .person-name {
    position: absolute;
    left: 0; right: 0; top: 224px;
    font-size: 24px;
    font-weight: 400;
    color: var(--name-red);
    text-transform: uppercase;
  }
  .person-title {
    position: absolute;
    left: 0; right: 0; top: 255px;
    font-size: 15px;
    color: var(--title-green);
  }
  .contact-email {
    position: absolute;
    left: 0; right: 0; top: 331px;
    font-size: 14px;
    display: flex;
    justify-content: center;
    align-items: center;
    gap: 14px;
  }
  .contact-email svg { width: 10px; height: 8px; }
  .locations {
    position: absolute;
    left: 0; right: 0; top: 400px;
    font-size: 15px;
    line-height: 16px;
  }
  .card-back {
    left: 645px;
    width: 305px;
    background: var(--gold);
  }
  .leaf-fill {
    position: absolute;
    right: 0; bottom: 0;
    width: 305px; height: 420px;
    background:
      radial-gradient(ellipse 60% 45% at 85% 70%, rgba(199,154,78,0.75), transparent 70%),
      radial-gradient(ellipse 50% 35% at 40% 88%, rgba(169,154,90,0.6), transparent 70%),
      radial-gradient(ellipse 30% 40% at 95% 25%, rgba(201,174,120,0.55), transparent 70%);
  }
  .back-mark {
    position: absolute;
    left: 76px; top: 124px;
    width: 160px; height: 160px;
    border: 6px solid var(--white);
    border-radius: 50%;
    display: flex;
    align-items: center;
    justify-content: center;
  }
  .back-mark span {
    color: var(--white);
    font-size: 17px;
    font-weight: 400;
  }
</style>
</head>
<body>
  <section class="card card-front">
    <div class="brand-circle"></div>
    <div class="brand-name">BrindlewayCare</div>
    <h1 class="person-name">Derek Mallow</h1>
    <p class="person-title">Executive Chairman</p>
    <p class="contact-email">
      <svg viewBox="0 0 10 8" aria-hidden="true">
        <rect x="0" y="0" width="10" height="8" fill="var(--name-red)"/>
        <path d="M0 0 L5 4.5 L10 0" fill="none" stroke="var(--card-white)" stroke-width="1"/>
      </svg>
      d.mallow@plumvora.example
    </p>
    <p class="locations">United Kingdom, Australia,<br>New Zealand</p>
  </section>

  <section class="card card-back">
    <div class="leaf-fill" role="img" aria-label="Soft autumn birch leaves scattered across the lower right of the card"></div>
    <div class="back-mark"><span>BrindlewayCare</span></div>
  </section>
</body>
</html>
```